Norrell Advisory WA Business Card

Create an interesting, eye catching and colourful two sided business card. We are a business consulting operation assisting SME's improve all areas of their business. We provide consulting services to assist SME's to create a culture of continuous improvement, making a positive difference in the business. Our tag line is Small changes, big rewards. We want to create a well recognised, innovative brand that can be continued throughout our website, social media and email correspondence.

Target Market(s)

Small to Medium Enterprise Business Owners

Industry/Entity Type

Business Consultant

Contact Information for Business Card

Name of Business: Norrell Advisory - Steady Steps Lasting Gains
Derek Holloway Ph 0407385510 Megan Holloway Ph 0407913847
Email norrelladvisorywa@mailbox-example.com
Web address TBA
FaceBook page TBA

BACKSIDE OF CARD

Providing assistance with:

• Organisation & Efficiency
• Revenue generation & Marketing
• Financial Management
• Production quality & delivery
• Systems & Process documentation
• Exit Strategy

Font styles to use
Other font styles liked:
• Calibri

Colors

Designer to choose colors to be used in the design.

Requirements
Must have
• Calibri font

```html
<!DOCTYPE html>
<html lang="en">
<head>
<meta charset="utf-8">
<title>Norrell Advisory – Business Card</title>
<link href="https://fonts.googleapis.com/css2?family=Carlito:wght@400;700&display=swap" rel="stylesheet">
<style>
  :root {
    --backdrop: #3b3b3b;
    --card: #2d2b2b;
    --white: #ffffff;
    --soft-white: #f1f1f1;
    --accent-blue: #1b80c4;
    --bullet-blue: #4aa3d8;
    --pastel-yellow: #fbe7a6;
    --pastel-green: #d3e6a8;
    --pastel-red: #f3a7a0;
    --pastel-blue: #a9d3ea;
  }
  * { margin: 0; padding: 0; box-sizing: border-box; }
  html, body {
    width: 1125px;
    height: 1200px;
    overflow: hidden;
    background: var(--backdrop);
    font-family: "Carlito", "Calibri", sans-serif;
  }
  .stage { position: relative; width: 1125px; height: 1200px; }
  .card {
    position: absolute;
    left: 157px;
    width: 826px;
    background: var(--card);
    box-shadow: 0 6px 18px rgba(0,0,0,0.45);
    overflow: hidden;
  }
  .card--front { top: 106px; height: 472px; }
  .card--back { top: 640px; height: 470px; }

  .pattern-band {
    position: absolute;
    left: 0;
    width: 100%;
    background: linear-gradient(180deg,
      var(--pastel-yellow) 0%,
      var(--pastel-green) 22%,
      var(--pastel-red) 50%,
      var(--pastel-blue) 75%,
      var(--pastel-yellow) 100%);
  }
  .pattern-band--top { top: 0; height: 159px; }
  .pattern-band--bottom { top: 353px; height: 119px;
    background: linear-gradient(180deg,
      var(--pastel-yellow) 0%,
      var(--pastel-green) 35%,
      var(--pastel-red) 70%,
      var(--pastel-blue) 100%); }

  .contact {
    position: absolute;
    top: 188px;
    left: 0;
    width: 100%;
    text-align: center;
    color: var(--white);
  }
  .contact__name { font-size: 37px; font-weight: 700; line-height: 1; letter-spacing: 0.5px; }
  .contact__phone { font-size: 23px; font-weight: 700; margin-top: 6px; line-height: 1; }
  .contact__line { font-size: 17.5px; margin-top: 15px; line-height: 1; color: var(--soft-white); }
  .contact__social-mark {
    display: inline-block;
    width: 14px; height: 14px;
    background: var(--white);
    vertical-align: -1px;
    margin: 0 4px 0 8px;
  }
  .contact__web { font-size: 17.5px; margin-top: 8px; letter-spacing: 2.2px; color: var(--soft-white); }

  .brand {
    position: absolute;
    left: 50px;
    top: 270px;
    width: 335px;
    text-align: center;
    color: var(--white);
  }
  .brand__name { font-size: 27px; font-weight: 700; letter-spacing: 0.5px; line-height: 1; }
  .brand__tagline { font-size: 15.5px; letter-spacing: 1.6px; margin-top: 5px; line-height: 1; }

  .services {
    position: absolute;
    left: 400px;
    top: 124px;
    color: var(--white);
  }
  .services__title { font-size: 28px; font-weight: 700; color: var(--accent-blue); line-height: 1; margin-bottom: 16px; }
  .services__list { list-style: none; }
  .services__item { font-size: 19.5px; line-height: 26.2px; display: flex; align-items: center; }
  .services__bullet {
    width: 12px; height: 12px;
    background: var(--bullet-blue);
    margin-right: 9px;
    flex: none;
  }
</style>
</head>
<body>
<main class="stage">
  <section class="card card--front">
    <div class="pattern-band pattern-band--top" role="img" aria-label="Band of pastel jigsaw puzzle pieces"></div>
    <div class="contact">
      <div class="contact__name">DEREK HOLLOWAY</div>
      <div class="contact__phone">0407385510</div>
      <div class="contact__line">norrelladvisorywa@mailbox-example.com<span class="contact__social-mark"></span>/ norrelladvisorywa</div>
      <div class="contact__web">www.norrelladvisorywa.com</div>
    </div>
    <div class="pattern-band pattern-band--bottom" role="img" aria-label="Band of pastel jigsaw puzzle pieces"></div>
  </section>

  <section class="card card--back">
    <div class="brand">
      <div class="brand__name">NORRELL ADVISORY</div>
      <div class="brand__tagline">STEADY STEPS LASTING GAINS</div>
    </div>
    <div class="services">
      <h2 class="services__title">Providing assistance with</h2>
      <ul class="services__list">
        <li class="services__item"><span class="services__bullet"></span>Organisation &amp; Efficiency</li>
        <li class="services__item"><span class="services__bullet"></span>Revenue generation &amp; Marketing</li>
        <li class="services__item"><span class="services__bullet"></span>Financial Management</li>
        <li class="services__item"><span class="services__bullet"></span>Production quality &amp; delivery</li>
        <li class="services__item"><span class="services__bullet"></span>Systems &amp; Process documentation</li>
        <li class="services__item"><span class="services__bullet"></span>Exit Strategy</li>
      </ul>
    </div>
  </section>
</main>
</body>
</html>
```